Website design and coding for new consultancy company

I need to have a full website designed for a new consultancy business I'm trying to establish. It's called BrightPath consult. I need an English version to begin with, and then there should be a Danish version as well, but I'll translate that myself. Just be aware that I need two language versions. The consultancy field that I'm targeting is Leadership - and specialist development. I offer to facilitate corporate academies for global companies as well as specific workshops within leadership- or team development, strategy sessions, personal coaching and facilitation of D&I (Diversity and inclusion) workshops. BTW my logo is not in high resolution - I need that as well.

Target Market(s)

Larger companies that has a need for developing their inhouse leadership capabilities or that wants to develop their specialists to take on more responsibility.

Industry/Entity Type

Consultancy business

Coding

Coded - Design and coding required

Number of Pages Required

5+ page

Requirements
Must have
• Introduction site with a catch phrase. Book a meeting. Services that's beeing offered. Blog site with white papers etc. Language toggle (Danish/English). Cases/testimonials. About site. Contact site.

```html
<!DOCTYPE html>
<html lang="en">
<head>
<meta charset="UTF-8">
<title>BrightPath consult</title>
<link href="https://fonts.googleapis.com/css2?family=Bebas+Neue&family=Montserrat:wght@400;500;600;700&display=swap" rel="stylesheet">
<style>
:root{
  --blue:#1e7bc4;
  --blue-dark:#1565a8;
  --ink:#1d1d1f;
  --muted:#6b6f76;
  --dark:#3a3f47;
  --white:#ffffff;
  --line:#cfd3d8;
  --soft:#eef4fa;
}
*{margin:0;padding:0;box-sizing:border-box}
html,body{width:1200px;height:3678px;overflow:hidden}
body{position:relative;font-family:'Montserrat',sans-serif;color:var(--ink);background:var(--white)}
.abs{position:absolute}
.backdrop{position:absolute;left:0;top:0}
.heading{font-family:'Bebas Neue',sans-serif;font-size:48px;letter-spacing:.5px;color:var(--ink);line-height:1}
.rule{height:4px;width:60px;background:var(--blue)}
.btn{position:absolute;display:flex;align-items:center;height:43px;background:var(--blue);color:var(--white);font-weight:700;font-size:14px;overflow:hidden}
.btn .label{padding-left:19px;flex:1}
.btn .tail{width:62px;height:100%;background:var(--white);clip-path:polygon(22% 0,100% 0,100% 100%,0 100%);display:flex;align-items:center;justify-content:center;border:2px solid var(--blue)}
/* header */
.site-header{left:0;top:0;width:1200px;height:79px;background:var(--white)}
.brand{font-weight:700;font-size:30px;letter-spacing:1px;color:var(--ink)}
.nav a{position:absolute;top:29px;font-size:13px;color:#444;text-decoration:none;font-weight:500}
.nav a.active{color:var(--blue);font-weight:600}
.call{left:1004px;top:0;width:196px;height:79px;background:var(--blue);clip-path:polygon(6% 0,100% 0,100% 100%,0 100%)}
.call-icon{left:1002px;top:18px;width:42px;height:42px;border-radius:50%;background:#222;display:flex;align-items:center;justify-content:center}
.call-text{left:1057px;top:14px;color:var(--white);font-size:16px;font-weight:500;line-height:23px}
/* hero */
.hero-title{left:0;top:160px;width:1200px;text-align:center;font-family:'Bebas Neue',sans-serif;font-size:58px;line-height:57px;color:var(--white)}
.hero-sub{left:0;top:286px;width:1200px;text-align:center;color:var(--white);font-size:16px}
.hero-btn{left:517px;top:330px;width:177px;height:44px;border:2px solid var(--white);display:flex;align-items:center;color:var(--white);font-weight:700;font-size:14px}
.hero-btn .label{padding-left:14px;flex:1}
.hero-btn .tail{width:50px;height:100%;background:var(--white);clip-path:polygon(22% 0,100% 0,100% 100%,0 100%);display:flex;align-items:center;justify-content:center}
/* about */
.about-text{left:624px;top:778px;width:410px;font-size:14px;line-height:25.7px;color:#555;text-align:justify}
/* expertise */
.card-main{left:117px;top:1331px;width:476px;height:452px;background:#2b2d31;border-radius:6px;overflow:hidden}
.card-title{left:136px;top:1576px;color:var(--white);font-size:22px;font-weight:600}
.card-text{left:136px;top:1619px;width:430px;color:#e4e4e4;font-size:13.5px;line-height:25.5px}
.card-slim{top:1331px;width:103px;height:452px;background:#2f3136;border-radius:6px;display:flex;align-items:center;justify-content:center}
.card-slim span{transform:rotate(-90deg);white-space:nowrap;color:var(--white);font-weight:600;font-size:21px;line-height:28px;text-align:center}
/* why */
.why-title{font-size:19px;font-weight:500}
.why-text{font-size:13px;line-height:26px;color:var(--muted)}
.why-icon{width:72px;height:72px;border-radius:50%;background:var(--white);box-shadow:0 4px 14px rgba(0,0,0,.12);display:flex;align-items:center;justify-content:center}
/* contact */
.contact-ic{width:72px;height:72px;border-radius:50%;background:#2b8fe0;display:flex;align-items:center;justify-content:center}
.contact-label{font-size:16px;font-weight:600}
.contact-val{font-size:16px;color:var(--muted);line-height:28px}
.form-card{left:614px;top:2686px;width:453px;height:545px;background:var(--white);border-top:3px solid var(--blue);box-shadow:0 6px 24px rgba(0,0,0,.1)}
.form-title{left:637px;top:2711px;font-size:19px;font-weight:600}
.field-label{font-size:13px;font-weight:600;left:646px}
.field-val{font-size:13px;color:var(--muted);left:646px}
.field-line{left:637px;width:401px;height:1px;background:var(--line)}
.field-icon{left:1008px}
/* footer */
.foot-note{font-size:12px;line-height:24px;text-align:center;color:#333}
.news-input{left:454px;top:3510px;width:346px;height:51px;border:1px solid #444;background:var(--white)}
.news-btn{left:751px;top:3510px;width:49px;height:51px;background:var(--blue);display:flex;align-items:center;justify-content:center}
.social{width:22px;height:22px;border-radius:50%;background:#1a1a1a;top:3522px}
.copyright{left:0;top:3638px;width:1186px;text-align:center;font-size:14px;color:#333}
</style>
</head>
<body>

<svg class="backdrop" width="1200" height="3678" viewBox="0 0 1200 3678">
  <defs>
    <linearGradient id="heroGrad" x1="0" y1="0" x2="1" y2="1">
      <stop offset="0" stop-color="#2c3846"/><stop offset=".5" stop-color="#3c4752"/><stop offset="1" stop-color="#1f2a35"/>
    </linearGradient>
    <linearGradient id="expGrad" x1="0" y1="0" x2="1" y2="1">
      <stop offset="0" stop-color="#3b4048"/><stop offset="1" stop-color="#33383f"/>
    </linearGradient>
    <linearGradient id="softGrad" x1="0" y1="0" x2="1" y2="1">
      <stop offset="0" stop-color="#f4f8fc"/><stop offset=".6" stop-color="#e9f1f9"/><stop offset="1" stop-color="#dce9f5"/>
    </linearGradient>
  </defs>
  <rect x="0" y="79" width="1200" height="540" fill="url(#heroGrad)" role="img" aria-label="Photo of a team meeting in a modern glass office"/>
  <polygon points="0,616 836,548 1200,616 1200,640 0,640" fill="#fff"/>
  <polygon points="0,586 836,527 1200,586 1200,616 836,548 0,616" fill="var(--blue)"/>

  <rect x="0" y="1064" width="1200" height="876" fill="url(#expGrad)" role="img" aria-label="Dark background photo of business growth charts"/>
  <polygon points="0,1060 1200,1060 1200,1066 364,1140 0,1066" fill="#fff"/>
  <polygon points="0,1066 364,1140 1200,1066 1200,1100 364,1156 0,1100" fill="var(--blue)"/>
  <polygon points="0,1936 836,1868 1200,1936 1200,1950 0,1950" fill="#fff"/>
  <polygon points="0,1900 836,1852 1200,1900 1200,1936 836,1868 0,1936" fill="var(--blue)"/>

  <rect x="0" y="2540" width="1200" height="846" fill="url(#softGrad)" role="img" aria-label="Soft light blue abstract network background"/>
  <polygon points="0,2530 1200,2530 1200,2556 364,2612 0,2556" fill="#fff"/>
  <polygon points="0,2520 364,2600 1200,2520 1200,2556 364,2612 0,2556" fill="var(--blue)"/>
  <polygon points="0,3385 836,3322 1200,3385 1200,3400 0,3400" fill="#fff"/>
  <polygon points="0,3350 836,3305 1200,3350 1200,3385 836,3322 0,3385" fill="var(--blue)"/>

  <!-- about portrait -->
  <circle cx="347" cy="864" r="197" fill="#dfe8f0" stroke="var(--blue)" stroke-width="4"/>
  <circle cx="347" cy="864" r="195" fill="#c9d6e2" role="img" aria-label="Portrait photo of the founder in a suit"/>
  <circle cx="489" cy="990" r="57" fill="#fff" stroke="var(--blue)" stroke-width="3"/>

  <!-- why choose us ring -->
  <path d="M497 2476 A157 157 0 1 1 703 2476" fill="none" stroke="var(--blue)" stroke-width="2"/>
  <circle cx="600" cy="2357" r="121" fill="#d9cfc3" role="img" aria-label="Photo of a business handshake"/>

  <!-- expertise card photo -->
  <rect x="117" y="1331" width="476" height="226" rx="6" fill="#5a5650" role="img" aria-label="Photo of a speaker presenting to an audience"/>
  <!-- dot grid -->
  <g fill="#1d1d1f">
    <circle cx="588" cy="2648" r="2"/><circle cx="602" cy="2648" r="2"/><circle cx="616" cy="2648" r="2"/><circle cx="630" cy="2648" r="2"/><circle cx="644" cy="2648" r="2"/><circle cx="658" cy="2648" r="2"/><circle cx="672" cy="2648" r="2"/><circle cx="686" cy="2648" r="2"/>
    <circle cx="588" cy="2662" r="2"/><circle cx="602" cy="2662" r="2"/><circle cx="616" cy="2662" r="2"/><circle cx="630" cy="2662" r="2"/><circle cx="644" cy="2662" r="2"/><circle cx="658" cy="2662" r="2"/><circle cx="672" cy="2662" r="2"/><circle cx="686" cy="2662" r="2"/>
    <circle cx="588" cy="2676" r="2"/><circle cx="602" cy="2676" r="2"/><circle cx="616" cy="2676" r="2"/><circle cx="630" cy="2676" r="2"/><circle cx="644" cy="2676" r="2"/><circle cx="658" cy="2676" r="2"/><circle cx="672" cy="2676" r="2"/><circle cx="686" cy="2676" r="2"/>
    <circle cx="588" cy="2690" r="2"/><circle cx="602" cy="2690" r="2"/>
    <circle cx="588" cy="2704" r="2"/><circle cx="602" cy="2704" r="2"/>
    <circle cx="588" cy="2718" r="2"/><circle cx="602" cy="2718" r="2"/>
    <circle cx="588" cy="2732" r="2"/><circle cx="602" cy="2732" r="2"/>
    <circle cx="588" cy="2746" r="2"/><circle cx="602" cy="2746" r="2"/>
    <circle cx="588" cy="2760" r="2"/><circle cx="602" cy="2760" r="2"/>
    <circle cx="588" cy="2774" r="2"/><circle cx="602" cy="2774" r="2"/>
    <circle cx="588" cy="2788" r="2"/><circle cx="602" cy="2788" r="2"/>
    <circle cx="588" cy="2802" r="2"/><circle cx="602" cy="2802" r="2"/>
  </g>
  <line x1="117" y1="3611" x2="1076" y2="3611" stroke="#888" stroke-width="1"/>
</svg>

<!-- header -->
<header class="abs site-header">
  <div class="abs brand" style="left:117px;top:20px">BRIGHTPATH</div>
  <nav class="nav">
    <a class="active" style="left:409px">HOME</a>
    <a style="left:480px">ABOUT US</a>
    <a style="left:579px">SERVICES</a>
    <a style="left:673px">WHY CHOOSE US</a>
    <a style="left:817px">CONTACT US</a>
    <a style="left:936px;font-weight:700;color:#222">EN
      <svg width="12" height="8" viewBox="0 0 12 8" style="margin-left:4px"><path d="M1 1l5 5 5-5" fill="none" stroke="#222" stroke-width="1.6"/></svg></a>
  </nav>
</header>
<div class="abs call"></div>
<div class="abs call-icon"><svg width="20" height="20" viewBox="0 0 24 24"><path d="M6.6 10.8a15 15 0 0 0 6.6 6.6l2.2-2.2c.3-.3.7-.4 1-.2 1.1.4 2.3.6 3.6.6.6 0 1 .4 1 1V20c0 .6-.4 1-1 1A17 17 0 0 1 3 4c0-.6.4-1 1-1h3.5c.6 0 1 .4 1 1 0 1.3.2 2.5.6 3.6.1.3 0 .7-.2 1z" fill="#fff"/></svg></div>
<div class="abs call-text">CALL US<br>+1 555 010 2020</div>

<!-- hero -->
<h1 class="abs hero-title">READY TO TURN YOUR PEOPLE INTO YOUR<br>GREATEST ASSET?</h1>
<p class="abs hero-sub">We facilitate leadership and specialist development, turning potential into performance.</p>
<div class="abs hero-btn"><span class="label">GET STARTED</span><span class="tail"><svg width="18" height="12" viewBox="0 0 18 12"><path d="M1 6h15M11 1l5 5-5 5" fill="none" stroke="var(--blue)" stroke-width="1.8"/></svg></span></div>

<!-- about -->
<h2 class="abs heading" style="left:624px;top:688px">ABOUT US</h2>
<div class="abs rule" style="left:624px;top:747px"></div>
<p class="abs about-text">In today's fast-paced business environment, sustainable success isn't just about strategy—it's about people. At BrightPath Consult, we specialize in developing the leaders and specialists who drive your organization forward. We partner with global companies to build robust leadership capabilities and cultivate the skills needed for tomorrow's challenges.</p>
<div class="btn" style="left:626px;top:983px;width:175px"><span class="label">READ MORE</span><span class="tail"><svg width="18" height="12" viewBox="0 0 18 12"><path d="M1 6h15M11 1l5 5-5 5" fill="none" stroke="var(--blue)" stroke-width="1.8"/></svg></span></div>

<!-- expertise -->
<h2 class="abs heading" style="left:0;top:1224px;width:1200px;text-align:center;color:#fff">OUR EXPERTISE</h2>
<div class="abs rule" style="left:570px;top:1284px"></div>
<div class="abs card-main"></div>
<svg class="abs" style="left:480px;top:1511px" width="92" height="92" viewBox="0 0 92 92">
  <circle cx="46" cy="46" r="44" fill="#2b2d31" stroke="var(--blue)" stroke-width="4"/>
  <circle cx="46" cy="46" r="34" fill="#3a3c41"/>
  <g fill="none" stroke="#fff" stroke-width="2"><rect x="32" y="30" width="28" height="30"/><path d="M38 36h4M50 36h4M38 44h4M50 44h4M42 60v-8h8v8"/></g>
</svg>
<h3 class="abs card-title">Corporate Academies</h3>
<p class="abs card-text">We design and facilitate comprehensive corporate academies that build a culture of continuous learning and development, from emerging leaders to seasoned executives.</p>
<div class="btn" style="left:139px;top:1711px;width:175px"><span class="label">READ MORE</span><span class="tail"><svg width="18" height="12" viewBox="0 0 18 12"><path d="M1 6h15M11 1l5 5-5 5" fill="none" stroke="var(--blue)" stroke-width="1.8"/></svg></span></div>
<div class="abs card-slim" style="left:611px"><span>Leadership &amp; Team<br>Development</span></div>
<div class="abs card-slim" style="left:733px"><span>Strategy Session</span></div>
<div class="abs card-slim" style="left:853px"><span>Personal Coaching</span></div>
<div class="abs card-slim" style="left:974px"><span>D&amp;I (Diversity &amp; Inclusion)<br>Workshops</span></div>

<!-- why choose us -->
<h2 class="abs heading" style="left:0;top:1974px;width:1200px;text-align:center">WHY CHOOSE US</h2>
<div class="abs rule" style="left:570px;top:2034px"></div>
<div class="abs why-title" style="left:0;top:2068px;width:1200px;text-align:center">Trusted</div>
<p class="abs why-text" style="left:0;top:2097px;width:1200px;text-align:center">Lorem Ipsum is simply dummy text of the<br>printing and typesetting industry.</p>

<div class="abs why-title" style="left:0;top:2222px;width:406px;text-align:right">Tailored, Not Templated</div>
<p class="abs why-text" style="left:0;top:2253px;width:406px;text-align:right">Lorem Ipsum is simply dummy text of the<br>printing and typesetting industry.</p>
<div class="abs why-title" style="left:793px;top:2222px">Experienced Professional</div>
<p class="abs why-text" style="left:798px;top:2253px">Lorem Ipsum is simply dummy text of the<br>printing and typesetting industry.</p>
<div class="abs why-title" style="left:0;top:2364px;width:366px;text-align:right">Holistic Human Development</div>
<p class="abs why-text" style="left:0;top:2396px;width:366px;text-align:right">Lorem Ipsum is simply dummy text of the<br>printing and typesetting industry.</p>
<div class="abs why-title" style="left:836px;top:2371px">Practical, Real-World Impact</div>
<p class="abs why-text" style="left:837px;top:2402px">Lorem Ipsum is simply dummy text of the<br>printing and typesetting industry.</p>

<div class="abs why-icon" style="left:564px;top:2164px"><svg width="40" height="40" viewBox="0 0 40 40" fill="none" stroke="var(--blue)" stroke-width="2"><path d="M6 22l8-8 6 4 8-8 6 6-12 12-6-4-4 4z"/><circle cx="30" cy="10" r="6"/></svg></div>
<div class="abs why-icon" style="left:425px;top:2233px"><svg width="40" height="40" viewBox="0 0 40 40" fill="none" stroke="var(--blue)" stroke-width="2"><circle cx="20" cy="20" r="12"/><circle cx="20" cy="20" r="5"/><path d="M20 4v6M20 30v6M4 20h6M30 20h6"/></svg></div>
<div class="abs why-icon" style="left:694px;top:2228px"><svg width="40" height="40" viewBox="0 0 40 40" fill="none" stroke="var(--blue)" stroke-width="2"><circle cx="20" cy="14" r="7"/><path d="M8 34c0-7 5-12 12-12s12 5 12 12"/><path d="M20 10v4l3 2"/></svg></div>
<div class="abs why-icon" style="left:397px;top:2368px"><svg width="40" height="40" viewBox="0 0 40 40" fill="none" stroke="var(--blue)" stroke-width="2"><path d="M6 34h28M10 34V24M17 34V18M24 34V22M31 34V12"/><path d="M8 18l8-7 7 5 10-9"/></svg></div>
<div class="abs why-icon" style="left:735px;top:2368px"><svg width="40" height="40" viewBox="0 0 40 40" fill="none" stroke="var(--blue)" stroke-width="2"><rect x="7" y="6" width="26" height="18" rx="2"/><circle cx="12" cy="30" r="3"/><circle cx="20" cy="30" r="3"/><circle cx="28" cy="30" r="3"/><path d="M12 13h16M12 18h10"/></svg></div>

<!-- contact -->
<h2 class="abs heading" style="left:117px;top:2710px">GET IN TOUCH</h2>
<div class="abs rule" style="left:117px;top:2769px"></div>
<div class="abs contact-ic" style="left:124px;top:2814px"><svg width="38" height="38" viewBox="0 0 38 38" fill="none" stroke="#fff" stroke-width="2"><rect x="4" y="8" width="30" height="22" rx="2"/><path d="M4 9l15 12 15-12M4 30l11-10M34 30L23 20"/></svg></div>
<div class="abs contact-ic" style="left:124px;top:2926px"><svg width="36" height="36" viewBox="0 0 24 24" fill="none" stroke="#fff" stroke-width="1.4"><path d="M6.6 10.8a15 15 0 0 0 6.6 6.6l2.2-2.2c.3-.3.7-.4 1-.2 1.1.4 2.3.6 3.6.6.6 0 1 .4 1 1V20c0 .6-.4 1-1 1A17 17 0 0 1 3 4c0-.6.4-1 1-1h3.5c.6 0 1 .4 1 1 0 1.3.2 2.5.6 3.6.1.3 0 .7-.2 1z"/></svg></div>
<div class="abs contact-ic" style="left:124px;top:3057px"><svg width="36" height="36" viewBox="0 0 36 36" fill="none" stroke="#fff" stroke-width="2"><path d="M18 33s-10-11-10-18a10 10 0 0 1 20 0c0 7-10 18-10 18z"/><circle cx="18" cy="15" r="4"/></svg></div>
<div class="abs contact-label" style="left:216px;top:2822px">Email Us</div>
<div class="abs contact-val" style="left:216px;top:2849px">info@brightpathconsult.com</div>
<div class="abs contact-label" style="left:216px;top:2936px">Contact Number</div>
<div class="abs contact-val" style="left:216px;top:2962px">+1 555 010 2020</div>
<div class="abs contact-label" style="left:216px;top:3052px">Location</div>
<div class="abs contact-val" style="left:216px;top:3079px">BrightPath consult , Lorem Ipsum<br>&nbsp;is simply dummy</div>

<div class="abs form-card"></div>
<div class="abs form-title">Drop your Message</div>
<div class="abs field-label" style="top:2758px">Name</div>
<div class="abs field-val" style="top:2786px">John</div>
<div class="abs field-line" style="top:2820px"></div>
<svg class="abs field-icon" style="top:2778px" width="20" height="20" viewBox="0 0 20 20" fill="none" stroke="#555" stroke-width="1.3"><circle cx="10" cy="6" r="4"/><path d="M3 19c0-4 3-7 7-7s7 3 7 7z"/></svg>
<div class="abs field-label" style="top:2845px">Email</div>
<div class="abs field-val" style="top:2872px">jane.doe@mail.com</div>
<div class="abs field-line" style="top:2907px"></div>
<svg class="abs field-icon" style="top:2866px" width="20" height="20" viewBox="0 0 20 20" fill="none" stroke="#555" stroke-width="1.3"><rect x="1" y="4" width="18" height="12"/><path d="M1 4l9 7 9-7"/></svg>
<div class="abs field-label" style="top:2932px">Phone Number</div>
<div class="abs field-val" style="top:2960px">+1 555 010 2020</div>
<div class="abs field-line" style="top:2994px"></div>
<svg class="abs field-icon" style="top:2955px" width="20" height="20" viewBox="0 0 24 24" fill="none" stroke="#555" stroke-width="1.3"><path d="M6.6 10.8a15 15 0 0 0 6.6 6.6l2.2-2.2c.3-.3.7-.4 1-.2 1.1.4 2.3.6 3.6.6.6 0 1 .4 1 1V20c0 .6-.4 1-1 1A17 17 0 0 1 3 4c0-.6.4-1 1-1h3.5c.6 0 1 .4 1 1 0 1.3.2 2.5.6 3.6.1.3 0 .7-.2 1z"/></svg>
<div class="abs field-label" style="top:3021px">Message</div>
<div class="abs field-val" style="top:3049px">Type Your Message</div>
<div class="abs field-line" style="top:3129px"></div>
<svg class="abs field-icon" style="top:3043px" width="20" height="20" viewBox="0 0 20 20" fill="none" stroke="#555" stroke-width="1.3"><circle cx="10" cy="10" r="8"/><circle cx="6.5" cy="10" r="1"/><circle cx="10" cy="10" r="1"/><circle cx="13.5" cy="10" r="1"/></svg>
<div class="btn" style="left:861px;top:3146px;width:176px"><span class="label" style="padding-left:36px">SUBMIT</span><span class="tail"><svg width="18" height="12" viewBox="0 0 18 12"><path d="M1 6h15M11 1l5 5-5 5" fill="none" stroke="var(--blue)" stroke-width="1.8"/></svg></span></div>

<!-- footer -->
<div class="abs brand" style="left:129px;top:3478px;font-size:34px">BRIGHTPATH</div>
<p class="abs foot-note" style="left:411px;top:3445px;width:400px">Subscribe to our newsletter to be the first to know about<br>special deals and promotions.</p>
<div class="abs news-input"></div>
<div class="abs news-btn"><svg width="20" height="20" viewBox="0 0 20 20" fill="none" stroke="#fff" stroke-width="1.4"><path d="M2 9l16-7-6 16-3-6z M9 12l9-10"/></svg></div>
<p class="abs foot-note" style="left:854px;top:3448px;width:200px">Follow us on social media to<br>stay up to date:</p>
<div class="abs social" style="left:876px" role="img" aria-label="Social network link"></div>
<div class="abs social" style="left:910px" role="img" aria-label="Social network link"></div>
<div class="abs social" style="left:945px" role="img" aria-label="Social network link"></div>
<div class="abs social" style="left:979px" role="img" aria-label="Social network link"></div>
<div class="abs social" style="left:1013px" role="img" aria-label="Social network link"></div>
<p class="abs copyright">Copyrights 2025.&nbsp; BrightPath .All Rights Reserved</p>

</body>
</html>
```